The Q Collective Business Cards

We need a sleek looking business card for our real estate company. Looking for a clean, modern, eye catching design on a standard size business card.
Updates

No more submissions please! Thank you!

Target Market(s)

General Public/Real Estate Clients

Industry/Entity Type

Real Estate

Contact Information for Business Card

Cards will be customized for each agent.

Colors

Designer to choose only greyscale colors for use in the design.

Requirements
Must have
• Black, white, gray color pallet, Photo area for headshot on the front of the card

```html
<!DOCTYPE html>
<html lang="en">
<head>
<meta charset="utf-8">
<title>The Q Collective – Agent Business Card</title>
<link rel="stylesheet" href="https://fonts.googleapis.com/css2?family=Mulish:wght@700&family=Roboto:wght@400;500&display=swap">
<style>
  :root {
    --page-bg: #d9d7d3;
    --card-bg: #ecebe8;
    --ink: #151515;
    --ink-soft: #2a2a2a;
    --photo-light: #d6ccc4;
    --photo-mid: #a8907f;
    --photo-dark: #5e4a3e;
    --bar: #111111;
  }
  html, body {
    margin: 0;
    padding: 0;
    width: 1200px;
    height: 1054px;
    overflow: hidden;
    background: var(--page-bg);
  }
  .card {
    position: absolute;
    left: 80px;
    top: 213px;
    width: 1040px;
    height: 628px;
    background: var(--card-bg);
    border-radius: 30px;
    overflow: hidden;
    box-shadow: 0 10px 30px rgba(0,0,0,0.12);
    font-family: "Roboto", Arial, sans-serif;
    color: var(--ink);
  }
  .headshot {
    position: absolute;
    left: 16px;
    top: 60px;
    width: 430px;
    height: 568px;
    border-radius: 200px 200px 0 0;
    background: radial-gradient(ellipse at 50% 35%, var(--photo-light) 0%, var(--photo-mid) 50%, var(--photo-dark) 100%);
    opacity: 0.85;
  }
  .brand {
    position: absolute;
    left: 462px;
    top: 80px;
    width: 508px;
    text-align: center;
  }
  .brand-name {
    display: flex;
    align-items: center;
    justify-content: center;
    gap: 16px;
    font-weight: 400;
    font-size: 44px;
    letter-spacing: 1px;
    line-height: 56px;
  }
  .brand-mark {
    width: 20px;
    height: 20px;
    background: var(--ink);
    flex: none;
  }
  .brand-tagline {
    margin-top: 32px;
    font-size: 20px;
    line-height: 24px;
    letter-spacing: 7px;
  }
  .agent {
    position: absolute;
    left: 549px;
    top: 262px;
  }
  .agent-name {
    font-family: "Mulish", Arial, sans-serif;
    font-weight: 700;
    font-size: 42px;
    line-height: 48px;
    margin: 0;
  }
  .agent-title {
    font-size: 25px;
    line-height: 34px;
    margin: 4px 0 0;
    color: var(--ink-soft);
  }
  .address {
    position: absolute;
    left: 549px;
    top: 386px;
    font-size: 25px;
    line-height: 39px;
    color: var(--ink-soft);
    font-style: normal;
  }
  .contacts {
    position: absolute;
    left: 549px;
    top: 474px;
    margin: 0;
    padding: 0;
    list-style: none;
    font-size: 25px;
    line-height: 40px;
    color: var(--ink-soft);
  }
  .contacts li {
    display: flex;
    align-items: center;
    height: 40px;
  }
  .contacts svg {
    width: 22px;
    height: 22px;
    margin-right: 31px;
    fill: var(--ink);
    flex: none;
  }
  .accent-bar {
    position: absolute;
    left: 524px;
    bottom: 0;
    width: 516px;
    height: 18px;
    background: var(--bar);
  }
</style>
</head>
<body>
  <article class="card">
    <div class="headshot" role="img" aria-label="Agent headshot photo"></div>

    <header class="brand">
      <div class="brand-name"><span class="brand-mark"></span>The Q Collective</div>
      <div class="brand-tagline">• REAL ESTATE TEAM •</div>
    </header>

    <div class="agent">
      <h1 class="agent-name">Maren Ellis Corbett</h1>
      <p class="agent-title">Real Estate Broker</p>
    </div>

    <address class="address">
      4120 Magnolia Pkwy<br>
      Riverton, LA, US 70812
    </address>

    <ul class="contacts">
      <li>
        <svg viewBox="0 0 24 24" aria-hidden="true"><path d="M3 8c0-2 3-4 9-4s9 2 9 4v2h-5V8H8v2H3zM6 12h12l2 8H4zm6 2a2.5 2.5 0 1 0 0 5 2.5 2.5 0 0 0 0-5z"/></svg>
        +1 225-555-0148
      </li>
      <li>
        <svg viewBox="0 0 24 24" aria-hidden="true"><path d="M2 5h20v14H2zm2 2v.5l8 5.5 8-5.5V7zm0 3v7h16v-7l-8 5.5z"/></svg>
        maren@riverhomesearch.com
      </li>
      <li>
        <svg viewBox="0 0 24 24" aria-hidden="true"><path d="M12 2a10 10 0 1 0 0 20 10 10 0 0 0 0-20zm-1 2.1V8H7.3A8 8 0 0 1 11 4.1zm2 0A8 8 0 0 1 16.7 8H13zM4.6 10H11v4H4.6a8 8 0 0 1 0-4zm8.4 0h6.4a8 8 0 0 1 0 4H13zm-5.7 6H11v3.9A8 8 0 0 1 7.3 16zm5.7 0h3.7A8 8 0 0 1 13 19.9z"/></svg>
        www.riverhomesearch.com
      </li>
    </ul>

    <div class="accent-bar"></div>
  </article>
</body>
</html>
```